New web design for a service provider in the medical field

We are looking for a new design for our website. We are a company that repairs and sells medical endoscopes. Our customers include doctors and hospitals. Our current website can be found at https://lumavex.de/en/lumavex-english.
We need a new web design (without programming) for the following 3 pages:
-Startpage https://lumavex.de/en/lumavex-english/
-Used endoscopes https://lumavex.de/en/used-endoscopes/
-Purchase https://lumavex.de/en/purchase/
The design should be modern and stylish.
The blue color of the logo should be reflected on the page, but not too intrusive.
I have uploaded the images from the header. If more images are needed, let me know and I will upload them.

Target Market(s)
Doctors and hospitals

```html
<!DOCTYPE html>
<html lang="en">
<head>
<meta charset="utf-8">
<title>Lumavex – Endoscope Repair and Sale</title>
<link rel="stylesheet" href="https://fonts.googleapis.com/css2?family=Poppins:wght@400;500;600;700;800&display=swap">
<style>
:root{
  --blue:#0a4fb4;
  --blue-deep:#063f9a;
  --blue-bright:#1a7be0;
  --blue-light:#5b9be6;
  --ink:#121212;
  --text:#5a5a5a;
  --muted:#8a8a8a;
  --pale:#e8eef8;
  --white:#ffffff;
}
*{box-sizing:border-box;margin:0;padding:0}
html,body{width:1200px;height:3500px;overflow:hidden}
body{position:relative;font-family:"Poppins",sans-serif;color:var(--ink);background:var(--white)}
.abs{position:absolute}
a{color:inherit;text-decoration:none}

/* header */
.site-header{position:absolute;left:0;top:0;width:1200px;height:88px;background:var(--white)}
.topbar{position:absolute;left:510px;top:0;width:690px;height:37px;background:var(--blue);border-radius:0 0 0 18px;display:flex;align-items:center;gap:18px;padding-left:42px;color:var(--white);font-size:10px}
.topbar .item{display:flex;align-items:center;gap:8px}
.topbar .sep{width:1px;height:16px;background:rgba(255,255,255,.7)}
.topbar .search{width:132px;border-bottom:1px solid rgba(255,255,255,.7);padding-bottom:2px;display:flex;justify-content:space-between}
.brand{position:absolute;left:100px;top:28px;display:flex;align-items:center;gap:8px;font-size:17px;font-weight:600;color:#333}
.brand .dot{width:12px;height:12px;border-radius:50%;background:var(--blue-bright)}
.main-nav{position:absolute;right:94px;top:55px;display:flex;gap:27px;font-size:11.5px;font-weight:600;color:#111}

/* hero */
.hero{position:absolute;left:0;top:88px;width:1200px;height:714px;overflow:hidden}
.hero-photo{position:absolute;inset:0;background:radial-gradient(ellipse at 55% 40%,#4fa0f5 0%,#1c6fe0 35%,#0a49c4 70%,#073aa3 100%)}
.hero h1{position:absolute;left:0;width:1200px;top:245px;text-align:center;font-size:47px;font-weight:800;color:var(--white);letter-spacing:-.5px;text-shadow:0 3px 6px rgba(0,0,0,.25)}
.hero p{position:absolute;left:140px;width:920px;top:312px;text-align:center;font-size:18.5px;line-height:30px;color:var(--white);font-weight:500}
.btn{position:absolute;display:flex;align-items:center;justify-content:center;border-radius:30px;font-weight:700;font-size:17px}
.btn-light{background:var(--white);color:var(--blue)}
.btn-dark{background:var(--blue-deep);color:var(--white)}
.hero-arrow{position:absolute;top:324px;width:30px;height:30px;border:2px solid var(--white);border-radius:50%}
.hero-dots{position:absolute;left:584px;top:640px;display:flex;gap:5px}
.hero-dots span{width:7px;height:7px;border-radius:50%;background:var(--white)}

/* about */
h2.section-title{font-size:30px;font-weight:700;color:var(--ink)}
.about-title{left:94px;top:912px}
.about-text{left:94px;top:965px;width:470px;font-size:13.5px;line-height:22.5px;color:var(--text)}
.about-text p+p{margin-top:22px}
.btn-sm{font-size:16px}
.about-photo{left:620px;top:874px;width:450px;height:375px;border-radius:22px;background:linear-gradient(135deg,#dfe3e8,#b9c1c9 55%,#e9ecef)}
.about-accent{left:840px;top:1082px;width:266px;height:200px}

/* services */
.center-title{left:0;width:1200px;text-align:center}
.center-sub{left:0;width:1200px;text-align:center;font-size:15px;color:var(--text)}
.service{position:absolute;width:300px;text-align:center}
.service-card{position:absolute;left:428px;top:1477px;width:337px;height:389px;background:var(--white);border-radius:14px;box-shadow:0 6px 22px rgba(0,0,0,.13)}
.icon-circle{width:90px;height:90px;border-radius:50%;background:#dfe9f6;margin:0 auto;display:flex;align-items:center;justify-content:center}
.service h3{font-size:22px;font-weight:600;margin-top:22px}
.service h4{font-size:19px;font-weight:500;color:#666;margin-top:6px}
.service p{font-size:13.5px;line-height:22px;color:var(--text);margin:14px auto 0;width:260px;height:66px;overflow:hidden}
.service .btn{position:relative;margin:16px auto 0;width:224px;height:40px;font-size:15px}

/* outcome */
.outcome-card{position:absolute;width:253px;height:316px;background:var(--white);border-radius:18px;box-shadow:0 6px 18px rgba(0,0,0,.12);text-align:center;padding-top:50px}
.outcome-card .pin{position:absolute;left:119px;top:-8px;width:16px;height:16px;border-radius:50%;background:var(--white);border:2px solid var(--blue)}
.outcome-icon{width:90px;height:90px;border-radius:50%;background:linear-gradient(135deg,#1d6fd6,#0a4fb4);margin:0 auto;display:flex;align-items:center;justify-content:center}
.outcome-card h3{font-size:17px;font-weight:600;color:#1765c7;line-height:22px;margin:28px 20px 0}
.outcome-card p{font-size:13.5px;line-height:21px;color:#222;margin:10px 26px 0}

/* used endoscopes */
.used-title{left:94px;top:2584px}
.used-text{left:94px;top:2634px;width:350px;font-size:13.5px;line-height:23.3px;color:var(--text)}
.round-arrow{position:absolute;top:2880px;width:24px;height:24px;border:1.5px solid #888;border-radius:50%}
.product{position:absolute;top:2570px;width:292px;height:356px;background:var(--white);box-shadow:0 4px 16px rgba(0,0,0,.12)}
.product .photo{height:187px}
.product h3{font-size:15px;font-weight:600;line-height:20px;margin:20px 14px 0;color:#111}
.product p{font-size:13.5px;line-height:21px;color:var(--text);margin:8px 14px 0}
.product a{display:block;font-size:13.5px;font-weight:600;color:var(--blue);margin:8px 16px 0}

/* cta */
.footer-bg{left:0;top:3099px;width:1200px;height:401px;background:var(--pale)}
.cta{left:94px;top:3014px;width:1012px;height:185px;border-radius:92px;background:linear-gradient(100deg,#1a8be8 0%,#0a63d0 45%,#0a4fb4 100%)}
.cta h2{position:absolute;left:79px;top:52px;font-size:30px;line-height:34px;font-weight:700;color:var(--white)}
.cta .btn{left:762px;top:71px;width:171px;height:42px;font-size:16px}

/* footer */
.footer-brand{left:100px;top:3288px;display:flex;align-items:center;gap:8px;font-size:16px;font-weight:600;color:#333}
.footer-brand .dot{width:11px;height:11px;border-radius:50%;background:var(--blue-bright)}
.footer-about{left:94px;top:3355px;width:290px;font-size:11.5px;line-height:21px;color:var(--text)}
.footer-col{position:absolute;top:3270px}
.footer-col h4{font-size:16px;font-weight:600;color:#111;margin-bottom:12px}
.footer-col li{list-style:none;font-size:11.5px;line-height:24.5px;color:var(--text)}
.subscribe{left:881px;top:3312px;width:225px;height:34px;border-radius:17px;background:var(--blue);border:1.5px solid var(--blue)}
.subscribe span{position:absolute;left:20px;top:8px;font-size:11.5px;color:var(--white)}
.subscribe b{position:absolute;right:0;top:0;width:104px;height:31px;border-radius:16px;background:var(--white);color:var(--blue);font-size:12.5px;font-weight:700;display:flex;align-items:center;justify-content:center}
.footer-mail{left:881px;top:3364px;display:flex;align-items:center;gap:10px;font-size:12px;font-weight:500;color:#111}
.to-top{left:1107px;top:3422px;width:40px;height:40px;border:2.5px solid var(--blue);border-radius:50%;display:flex;align-items:center;justify-content:center}
.copyright{left:0;top:3463px;width:1200px;text-align:center;font-size:12.5px;color:#222}
</style>
</head>
<body>

<header class="site-header">
  <div class="brand"><span class="dot"></span>Lumavex</div>
  <div class="topbar">
    <span class="item">
      <svg width="12" height="12" viewBox="0 0 24 24"><path fill="#fff" d="M6.6 10.8a15 15 0 0 0 6.6 6.6l2.2-2.2c.3-.3.7-.4 1-.2 1.1.4 2.3.6 3.6.6.6 0 1 .4 1 1V20c0 .6-.4 1-1 1A17 17 0 0 1 3 4c0-.6.4-1 1-1h3.5c.6 0 1 .4 1 1 0 1.3.2 2.5.6 3.6.1.3 0 .7-.2 1z"/></svg>
      Call Us : +49 4020 555 170-0</span>
    <span class="sep"></span>
    <span class="item">
      <svg width="16" height="11" viewBox="0 0 16 11"><rect x=".5" y=".5" width="15" height="10" fill="none" stroke="#fff"/><path d="M.5.5 8 6l7.5-5.5" fill="none" stroke="#fff"/></svg>
      Email Now : info@lumavex.de</span>
    <span class="sep"></span>
    <span class="search">Search Here......
      <svg width="11" height="11" viewBox="0 0 12 12"><circle cx="7" cy="5" r="3.8" fill="none" stroke="#fff" stroke-width="1.4"/><path d="M4.3 7.7 1 11" stroke="#fff" stroke-width="1.4"/></svg></span>
  </div>
  <nav class="main-nav">
    <a>Home</a><a>Endoscope Repair</a><a>Used Endoscopes</a><a>Endoscopy Systems</a><a>Endoscopy Accessories</a><a>Purchase</a>
  </nav>
</header>

<section class="hero">
  <div class="hero-photo" role="img" aria-label="Flexible endoscope coiled against a blue medical backdrop"></div>
  <h1>PUT YOUR ENDOSCOPE IN RELIABLE HANDS!</h1>
  <p>Lumavex GmbH is specialised in the repair and sale of Altora, Pemrix and Kenzura flexible medical endoscopes. As a service-oriented company, we are at your side with our knowledge and skills!</p>
  <a class="btn btn-light" style="left:382px;top:402px;width:206px;height:43px">PICK-UP ORDER</a>
  <a class="btn btn-dark" style="left:612px;top:402px;width:206px;height:43px">CONTACT NOW</a>
  <span class="hero-arrow" style="left:41px"><svg width="26" height="26" viewBox="0 0 26 26"><path d="M15 7l-6 6 6 6" fill="none" stroke="#fff" stroke-width="2"/></svg></span>
  <span class="hero-arrow" style="left:1132px"><svg width="26" height="26" viewBox="0 0 26 26"><path d="M11 7l6 6-6 6" fill="none" stroke="#fff" stroke-width="2"/></svg></span>
  <div class="hero-dots"><span></span><span></span><span></span></div>
  <svg class="abs" style="left:0;top:636px" width="1200" height="78" viewBox="0 0 1200 78">
    <polygon points="0,0 560,36 1200,16 1200,78 0,78" fill="#7aa8df"/>
    <polygon points="0,68 1200,26 1200,78 0,78" fill="#fff"/>
  </svg>
</section>

<h2 class="section-title abs about-title">ABOUT US</h2>
<div class="abs about-text">
  <p>Lumavex GmbH is specialized in repairing and saling flexible endoscopes along with accessories and consumables. We offer endoscopes, processors, light sources, accessories and much more – with a focus on the manufacturers Altora, Pemrix and Kenzura.</p>
  <p>We applied for foundation in 2020, whereby Lumavex emerged from another company in the same business field. For this reason, all employees have many years of experience. Lumavex is a reliable contact for doctors and hospitals.</p>
</div>
<a class="btn btn-dark btn-sm" style="left:94px;top:1196px;width:134px;height:42px;background:var(--blue)">READ MORE</a>
<svg class="abs about-accent" viewBox="0 0 266 200"><path d="M250 0 266 0 266 200 0 200 20 170 230 170 250 150Z" fill="var(--blue)"/></svg>
<div class="abs about-photo" role="img" aria-label="Technician in a lab coat handling an endoscope next to an endoscopy tower"></div>

<h2 class="section-title abs center-title" style="top:1364px">YOUR FUTURE - OUR SERVICE</h2>
<p class="abs center-sub" style="top:1412px">Endoscope repairs and second hand endoscopes from Lumavex – cause the outcome matters!</p>

<div class="service-card"></div>
<div class="service" style="left:104px;top:1485px">
  <div class="icon-circle"><svg width="50" height="50" viewBox="0 0 50 50"><path d="M10 40 34 16M34 8a8 8 0 0 0 8 12M8 10l30 30" stroke="var(--blue)" stroke-width="6" stroke-linecap="round" fill="none"/></svg></div>
  <h3>Repair</h3><h4>Endoscope repair service</h4>
  <p>Manufacturer-independent we repair and maintain endoscopes, individual components</p>
  <a class="btn btn-dark" style="background:var(--blue)">REPAIR REQUEST</a>
</div>
<div class="service" style="left:445px;top:1519px">
  <div class="icon-circle"><svg width="50" height="50" viewBox="0 0 50 50"><circle cx="18" cy="32" r="11" fill="var(--blue)"/><ellipse cx="34" cy="36" rx="10" ry="5" fill="var(--blue)"/><path d="M32 26V8M26 14l6-6 6 6M42 26V14M38 18l4-4 4 4" stroke="var(--blue)" stroke-width="3" fill="none"/></svg></div>
  <h3>Sale</h3><h4>Used endoscopes</h4>
  <p>Our regular stock includes refurbished gastroscopes, coloscopes, bronchoscopes, cystoscopes and</p>
  <a class="btn btn-dark" style="background:var(--blue)">PURCHASE REQUEST</a>
</div>
<div class="service" style="left:786px;top:1485px">
  <div class="icon-circle"><svg width="50" height="50" viewBox="0 0 50 50"><path d="M6 10h7l5 20h22l4-14H16" stroke="var(--blue)" stroke-width="4" fill="none"/><path d="M16 16h28l-4 14H18z" fill="var(--blue)"/><circle cx="20" cy="40" r="4" fill="var(--blue)"/><circle cx="36" cy="40" r="4" fill="var(--blue)"/></svg></div>
  <h3>Purchase</h3><h4>Used endoscopes</h4>
  <p>We are very interested in buying your old endoscopes – even defective and dismantled!</p>
  <a class="btn btn-dark" style="background:var(--blue)">SELL DEVICE</a>
</div>

<svg class="abs" style="left:0;top:1893px" width="1200" height="648" viewBox="0 0 1200 648">
  <defs><linearGradient id="band" x1="0" x2="1"><stop offset="0" stop-color="#0a4fb4"/><stop offset="1" stop-color="#0c6fd6"/></linearGradient></defs>
  <polygon points="0,0 430,330 0,648" fill="url(#band)"/>
  <polygon points="1200,34 770,330 1200,648" fill="url(#band)"/>
  <rect x="0" y="254" width="1200" height="163" fill="url(#band)"/>
</svg>
<h2 class="section-title abs center-title" style="top:1953px">CAUSE THE OUTCOME MATTERS!</h2>
<p class="abs center-sub" style="top:2002px">Our service includes the manufacturers Altora, Pemrix and Kenzura!</p>

<div class="outcome-card" style="left:67px;top:2077px"><span class="pin"></span>
  <div class="outcome-icon"><svg width="46" height="46" viewBox="0 0 46 46"><path d="M14 6v12a8 8 0 0 0 16 0V6M22 26v6a8 8 0 0 0 16 0v-6" stroke="#fff" stroke-width="2.5" fill="none"/><circle cx="38" cy="22" r="4" stroke="#fff" stroke-width="2.5" fill="none"/><circle cx="12" cy="36" r="3" stroke="#fff" stroke-width="2" fill="none"/></svg></div>
  <h3>ONE COMPANY FOR EVERYONE</h3><p>We are a service provider for doctors and hospitals!</p></div>
<div class="outcome-card" style="left:337px;top:2130px"><span class="pin"></span>
  <div class="outcome-icon"><svg width="46" height="46" viewBox="0 0 46 46"><circle cx="23" cy="20" r="6" fill="#fff"/><path d="M11 38a12 12 0 0 1 24 0z" fill="#fff"/><circle cx="10" cy="22" r="3.5" fill="#fff"/><circle cx="36" cy="22" r="3.5" fill="#fff"/><path d="M23 4l1.5 3 3 .4-2.2 2 .6 3-2.9-1.5-2.9 1.5.6-3-2.2-2 3-.4z" fill="#fff"/></svg></div>
  <h3>EXPERIENCE CHARACTERISES US</h3><p>Our team has many years of experience in the business field!</p></div>
<div class="outcome-card" style="left:610px;top:2077px"><span class="pin"></span>
  <div class="outcome-icon"><svg width="46" height="46" viewBox="0 0 46 46"><path d="M26 8c10 0 14 8 12 16s-10 14-18 12" stroke="#fff" stroke-width="2.5" fill="none"/><rect x="8" y="14" width="16" height="16" rx="4" stroke="#fff" stroke-width="2.5" fill="none"/><path d="M16 18v8M12 22h8" stroke="#fff" stroke-width="2.5"/></svg></div>
  <h3>THE PRODUCT IS CLOSE TO OUR HEARTS</h3><p>We repair and sell second hand, flexible endoscopes!</p></div>
<div class="outcome-card" style="left:882px;top:2130px"><span class="pin"></span>
  <div class="outcome-icon"><svg width="46" height="46" viewBox="0 0 46 46"><circle cx="20" cy="26" r="10" stroke="#fff" stroke-width="5" stroke-dasharray="4 3" fill="none"/><circle cx="20" cy="26" r="4" fill="#fff"/><circle cx="33" cy="13" r="6" stroke="#fff" stroke-width="3.5" stroke-dasharray="3 2" fill="none"/></svg></div>
  <h3>SERVICES FOR EVERYONE</h3><p>Our service includes the manufacturers Altora, Pemrix and Kenzura!</p></div>

<h2 class="section-title abs used-title">USED ENDOSCOPES</h2>
<p class="abs used-text">It is a long established fact that a reader will be distracted by the readable content of a page when looking at its layout. The point of using Lorem Ipsum is that it has a more-or-less normal distribution of letters, as opposed to using 'Content here, content here', making it look like readable English. Many desktop publishing packages and web page editors now use Lorem Ipsum as their default model text</p>
<span class="round-arrow" style="left:94px"><svg width="21" height="21" viewBox="0 0 21 21"><path d="M12 6l-4.5 4.5L12 15" fill="none" stroke="#777" stroke-width="1.5"/></svg></span>
<span class="round-arrow" style="left:130px"><svg width="21" height="21" viewBox="0 0 21 21"><path d="M9 6l4.5 4.5L9 15" fill="none" stroke="#777" stroke-width="1.5"/></svg></span>

<article class="product" style="left:489px">
  <div class="photo" role="img" aria-label="Clinicians in scrubs performing an endoscopy" style="background:linear-gradient(135deg,#7fc7dc,#2f86b8 60%,#1e5d8e)"></div>
  <h3>Second hand Altora-endoscopes and -processors</h3>
  <p>Lumavex GmbH offers you excellent second hand Altora equipment (endoscopes and processors)</p>
  <a>Read More</a>
</article>
<article class="product" style="left:813px">
  <div class="photo" role="img" aria-label="Endoscopy monitor and processor in a procedure room" style="background:linear-gradient(135deg,#3b3f4a,#7a5a48 45%,#c9cdd3)"></div>
  <h3>Second hand Pemrix-endoscopes and -processors</h3>
  <p>Our second hand Pemrix equipment (endoscopes and processors) is an high-quality and cost-effective</p>
  <a>Read More</a>
</article>

<div class="abs footer-bg"></div>
<div class="abs cta">
  <h2>JOIN NOW, FOR GET&nbsp; MORE DETAILS ON<br>OUR SERVICES</h2>
  <a class="btn btn-light">GET IN TOUCH</a>
</div>

<div class="abs footer-brand"><span class="dot"></span>Lumavex</div>
<p class="abs footer-about">Lumavex GmbH is specialised in the repair and sale of Altora, Pemrix and Kenzura flexible medical endoscopes.</p>
<div class="footer-col" style="left:434px"><h4>QUICK LINKS</h4><ul><li>Home</li><li>About Us</li><li>Purchase</li><li>Pick-Up Order</li><li>Contact Us</li></ul></div>
<div class="footer-col" style="left:646px"><h4>INFORMATION LINKS</h4><ul><li>Endoscope Repair</li><li>Used Endoscopes</li><li>Endoscopy Systems</li><li>Endoscopy Accessories</li><li>Terms &amp; Conditions</li></ul></div>
<div class="footer-col" style="left:881px"><h4>STAY CONNECTED</h4></div>
<div class="abs subscribe"><span>Email Address</span><b>SEND NOW</b></div>
<div class="abs footer-mail"><svg width="16" height="11" viewBox="0 0 16 11"><rect x=".5" y=".5" width="15" height="10" fill="none" stroke="#111"/><path d="M.5.5 8 6l7.5-5.5" fill="none" stroke="#111"/></svg>info@lumavex.de</div>
<div class="abs to-top"><svg width="20" height="20" viewBox="0 0 20 20"><path d="M4 13l6-6 6 6" fill="none" stroke="var(--blue)" stroke-width="2.5"/></svg></div>
<p class="abs copyright">Copyright © 2022 Lumavex GmbH</p>

</body>
</html>
```